BUSINESS CARD DESIGN

NAME- DALE VORSKIN
PHONE NUMER - 555- 714-9082
EMAIL- OFFICE@TRV-GROUNDMAKRZ.COM
BACK OF CARD- SPEACIALIZES IN LAND CLEARING, FORESTRY MUCLHING AND EXCAVATION

Contact Information for Business Card

NAME- DALE VORSKIN PHONE NUMER - 555- 714-9082 EMAIL- OFFICE@TRV-GROUNDMAKRZ.COM BACK OF CARD- SPEACIALIZES IN LAND CLEARING , MUCLHING AND EXCAVATION

```html
<!DOCTYPE html>
<html lang="en">
<head>
<meta charset="utf-8">
<title>Trevally Groundmakrz LLC – Business Card</title>
<link href="https://fonts.googleapis.com/css2?family=Lato:wght@400;700;900&display=swap" rel="stylesheet">
<style>
  :root {
    --stage: #3a3a3c;
    --card-dark: #1c1c1e;
    --card-dark-edge: #2a2a2d;
    --silver: #e4e4e6;
    --silver-soft: #b9b9bd;
    --ink: #111111;
    --paper: #ffffff;
    --rule-blue: #262a44;
  }
  * { box-sizing: border-box; margin: 0; padding: 0; }
  html, body { width: 1200px; height: 694px; overflow: hidden; }
  body {
    background: var(--stage);
    font-family: 'Lato', Arial, sans-serif;
    display: flex;
    align-items: center;
    justify-content: center;
    gap: 40px;
  }
  .card {
    width: 540px;
    height: 310px;
    border-radius: 18px;
    position: relative;
    overflow: hidden;
  }

  /* Back of card */
  .card-back {
    background: linear-gradient(160deg, var(--card-dark-edge), var(--card-dark));
    color: var(--silver);
  }
  .card-back .edge-rule {
    position: absolute; left: 38px; top: 0; bottom: 0;
    width: 1px; background: var(--rule-blue);
  }
  .card-back .brand {
    position: absolute; top: 70px; left: 0; right: 0;
    display: flex; flex-direction: column; align-items: center; gap: 10px;
  }
  .brand-row { display: flex; align-items: center; gap: 14px; }
  .brand-dot {
    width: 44px; height: 44px; border-radius: 50%;
    border: 2px solid var(--silver);
  }
  .brand-name {
    font-weight: 900; font-size: 26px; letter-spacing: 2px; line-height: 1.1;
  }
  .brand-sub {
    font-weight: 900; font-size: 13px; letter-spacing: 6px;
  }
  .card-back .tagline {
    position: absolute; bottom: 48px; left: 0; right: 0;
    text-align: center; font-size: 16px; color: var(--silver);
  }

  /* Front of card */
  .card-front { background: var(--paper); color: var(--ink); }
  .card-front .top-bar {
    position: absolute; top: 0; right: 0; width: 10px; height: 58px;
    background: var(--ink);
  }
  .person {
    position: absolute; top: 26px; right: 34px; text-align: right;
  }
  .person-name { font-weight: 900; font-size: 22px; letter-spacing: 0.2px; }
  .person-role { font-size: 13px; margin-top: 2px; }

  .front-brand {
    position: absolute; top: 48px; left: 30px;
  }
  .front-brand .brand-name { font-size: 22px; color: var(--ink); }
  .front-brand .brand-sub { font-size: 11px; color: var(--ink); margin-top: 6px; }

  .mark-area {
    position: absolute; right: 40px; top: 100px;
    width: 170px; height: 170px; border-radius: 50%;
    border: 6px solid var(--ink);
  }

  .contacts {
    position: absolute; left: 30px; bottom: 76px;
    list-style: none; font-size: 13px; line-height: 1.55;
  }
  .contacts li { display: flex; align-items: center; gap: 8px; }
  .contacts svg { width: 12px; height: 12px; flex: none; fill: var(--ink); }
  .address {
    position: absolute; left: 30px; bottom: 24px;
    font-size: 13px; line-height: 1.45;
  }
</style>
</head>
<body>

  <section class="card card-back" aria-label="Back of business card">
    <div class="edge-rule"></div>
    <div class="brand">
      <div class="brand-row">
        <span class="brand-dot"></span>
        <span class="brand-name">TREVALLY GROUNDMAKRZ</span>
      </div>
      <span class="brand-sub">LLC · HAWAII · 555-714-9082</span>
    </div>
    <p class="tagline">Speacializes In Land Clearing , Muclhing And Excavation</p>
  </section>

  <section class="card card-front" aria-label="Front of business card">
    <div class="top-bar"></div>
    <div class="person">
      <div class="person-name">DALE VORSKIN</div>
      <div class="person-role">Owner</div>
    </div>

    <div class="front-brand">
      <div class="brand-name">TREVALLY<br>GROUNDMAKRZ</div>
      <div class="brand-sub">LLC · HAWAII · 555-714-9082</div>
    </div>

    <div class="mark-area"></div>

    <ul class="contacts">
      <li>
        <svg viewBox="0 0 12 12" aria-hidden="true"><path d="M2.5 0.8 L4.4 3 L3.4 4.3 Q4.6 6.9 7.6 8.6 L8.9 7.6 L11.2 9.5 L10 11.2 Q4.6 10.8 0.8 2 Z"/></svg>
        555- 714-9082
      </li>
      <li>
        <svg viewBox="0 0 12 12" aria-hidden="true"><path d="M0.5 2.5 H11.5 V9.5 H0.5 Z M0.5 2.5 L6 6.6 L11.5 2.5" fill="none" stroke="#111" stroke-width="1.2"/></svg>
        Office@trv-groundmakrz.com
      </li>
      <li>
        <svg viewBox="0 0 12 12" aria-hidden="true"><circle cx="6" cy="6" r="5.2" fill="none" stroke="#111" stroke-width="1.1"/><path d="M0.8 6 H11.2 M6 0.8 Q3 6 6 11.2 M6 0.8 Q9 6 6 11.2" fill="none" stroke="#111" stroke-width="0.9"/></svg>
        www.websitename.com
      </li>
    </ul>
    <p class="address">421, Address line goes here<br>45452, Country name</p>
  </section>

</body>
</html>
```